Health and wellnes company needs business cards

We are a Health and wellness business just relocated to Spain. Here nobody knows our business so we would like to put some of our services on the card. Clean design with logo.

Contact Information for Business Card

Brightmeadow
Paula & Oskar Dunbeck
Calle del Almendro 57
Villamar de la Costa
Mobile: 0046 731 402687
info@brightmeadow.example

Font styles to use
Serif

Colors
85cae6
85acd3
b768aa

Requirements
Must have
• these Services somewhere on the card
• - Private or group yoga
• - Reconnective healing
• - Kitesurfing lessons
• - Massage
• LOgo somewhere
Nice to have
• Colours that go with the logo please

```html
<!DOCTYPE html>
<html lang="en">
<head>
<meta charset="utf-8">
<title>Brightmeadow business card</title>
<link rel="stylesheet" href="https://fonts.googleapis.com/css2?family=Marcellus&family=Lato:wght@400&family=Poppins:wght@400&display=swap">
<style>
  :root {
    --navy: #173a66;
    --teal: #6cc4c9;
    --white: #ffffff;
    --ink: #3c4a5c;
    --backdrop: #e9ebee;
  }
  html, body {
    margin: 0;
    padding: 0;
    width: 1200px;
    height: 862px;
    overflow: hidden;
    background: var(--backdrop);
  }
  .canvas {
    position: relative;
    width: 1200px;
    height: 862px;
  }
  .card {
    position: absolute;
    top: 154px;
    width: 318px;
    height: 556px;
    border-radius: 74px 6px 74px 6px;
    box-shadow: 0 6px 18px rgba(0,0,0,0.18);
    text-align: center;
    box-sizing: border-box;
  }
  .card-front {
    left: 312px;
    background: var(--navy);
    color: var(--white);
  }
  .card-back {
    left: 665px;
    background: var(--white);
    color: var(--navy);
  }
  .brand-dot {
    position: absolute;
    left: 50%;
    border-radius: 50%;
    transform: translateX(-50%);
    border: 6px solid var(--teal);
    box-sizing: border-box;
  }
  .card-front .brand-dot {
    top: 206px;
    width: 92px;
    height: 92px;
  }
  .card-back .brand-dot {
    top: 80px;
    width: 100px;
    height: 100px;
  }
  .brand-name {
    position: absolute;
    left: 0;
    right: 0;
    margin: 0;
    font-family: "Marcellus", serif;
    font-weight: 400;
    letter-spacing: 0.5px;
    line-height: 1;
  }
  .card-front .brand-name {
    top: 312px;
    font-size: 27px;
    color: var(--white);
  }
  .card-back .brand-name {
    top: 192px;
    font-size: 28px;
    color: var(--navy);
  }
  .services {
    position: absolute;
    left: 0;
    right: 0;
    top: 436px;
    margin: 0;
    font-family: "Lato", sans-serif;
    font-size: 12.5px;
    line-height: 20px;
    color: var(--white);
  }
  .services .sep { opacity: 0.7; padding: 0 2px; }
  .owners {
    position: absolute;
    left: 0;
    right: 0;
    top: 290px;
    margin: 0;
    font-family: "Marcellus", serif;
    font-size: 20px;
    line-height: 30px;
    color: var(--navy);
  }
  .contact {
    position: absolute;
    left: 0;
    right: 0;
    top: 374px;
    font-family: "Poppins", sans-serif;
    font-size: 13px;
    color: var(--ink);
    line-height: 20px;
  }
  .contact-line {
    display: flex;
    justify-content: center;
    align-items: center;
    gap: 7px;
  }
  .contact-line svg { width: 11px; height: 11px; }
  .divider {
    width: 16px;
    height: 2px;
    background: var(--teal);
    margin: 8px auto 7px;
  }
  .address { margin: 0; }
</style>
</head>
<body>
<div class="canvas">
  <section class="card card-front">
    <span class="brand-dot"></span>
    <h1 class="brand-name">BRIGHTMEADOW</h1>
    <p class="services">
      Private or group yoga <span class="sep">|</span> Reconnective healing<br>
      Kitesurfing lessons <span class="sep">|</span> Massage <span class="sep">|</span> LOgo somewhere
    </p>
  </section>

  <section class="card card-back">
    <span class="brand-dot"></span>
    <h2 class="brand-name">BRIGHTMEADOW</h2>
    <p class="owners">PAULA &amp;<br>OSKAR DUNBECK</p>
    <div class="contact">
      <div class="contact-line">
        <svg viewBox="0 0 24 24" aria-hidden="true"><path fill="#6cc4c9" d="M6.6 10.8a15.1 15.1 0 0 0 6.6 6.6l2.2-2.2c.3-.3.7-.4 1-.2 1.1.4 2.3.6 3.6.6.6 0 1 .4 1 1V20c0 .6-.4 1-1 1A17 17 0 0 1 3 4c0-.6.4-1 1-1h3.5c.6 0 1 .4 1 1 0 1.3.2 2.5.6 3.6.1.3 0 .7-.2 1z"/></svg>
        <span>0046 731 402687</span>
      </div>
      <div class="contact-line">
        <svg viewBox="0 0 24 24" aria-hidden="true"><rect x="2.5" y="5" width="19" height="14" fill="none" stroke="#6cc4c9" stroke-width="2"/><path d="M3 6l9 7 9-7" fill="none" stroke="#6cc4c9" stroke-width="2"/></svg>
        <span>info@brightmeadow.example</span>
      </div>
      <div class="divider"></div>
      <p class="address">Calle del Almendro 57<br>Villamar de la Costa</p>
    </div>
  </section>
</div>
</body>
</html>
```